SkyvornQ Business Cards and Stationary Design

Need a design for our business cards and stationary. I want to carry on the theme of the logo. I want the business cards to have a design on the back. I would like the business cards and the stationary to carry the same theme, design scheme, and branding

Target Market(s)

Airlines and Maintenance Facilities

Industry/Entity Type

Aviation

Contact Information for Business Card

Name
Position Title
Address: 4827 Trellis Hollow Road, Corvale Bay, Westmarch, 34951
Office Number
Mobile Number
Email
Website

Font styles to use
Serif
Sans Serif

Colors

Designer to choose colors to be used in the design.

```html
<!DOCTYPE html>
<html lang="en">
<head>
<meta charset="utf-8">
<title>SkyvornQ Business Card</title>
<link rel="stylesheet" href="https://fonts.googleapis.com/css2?family=Montserrat:wght@400;500;700;800&display=swap">
<style>
  :root {
    --navy-deep: #14264f;
    --navy: #1c3163;
    --navy-light: #2b4478;
    --sky: #2f7fc8;
    --white: #ffffff;
    --grey: #6d7380;
    --backdrop: #e9eaed;
  }
  * { margin: 0; padding: 0; box-sizing: border-box; }
  html, body { width: 1200px; height: 930px; overflow: hidden; }
  body {
    background: var(--backdrop);
    font-family: "Montserrat", sans-serif;
    position: relative;
  }
  .card {
    position: absolute;
    left: 290px;
    width: 620px;
    height: 354px;
    border-radius: 18px;
    overflow: hidden;
    box-shadow: 0 10px 30px rgba(0,0,0,0.18);
  }
  .card--front {
    top: 60px;
    background: linear-gradient(120deg, var(--navy) 0%, var(--navy-light) 50%, var(--navy-deep) 100%);
    color: var(--white);
    display: flex;
    flex-direction: column;
    align-items: center;
    justify-content: center;
  }
  .front-mark {
    display: flex;
    align-items: center;
    gap: 18px;
  }
  .front-mark__circle {
    width: 58px; height: 58px;
    border: 6px solid var(--white);
    border-radius: 50%;
  }
  .front-mark__name {
    font-weight: 800;
    font-size: 50px;
    letter-spacing: 6px;
  }
  .front-url {
    margin-top: 26px;
    font-size: 15px;
    font-weight: 500;
    letter-spacing: 0.5px;
  }
  .card--back {
    top: 516px;
    background: var(--white);
  }
  .back-band { position: absolute; inset: 0; }
  .back-wordmark {
    position: absolute;
    top: 34px; right: 44px;
    font-weight: 800;
    font-size: 34px;
    letter-spacing: 5px;
    color: var(--navy);
  }
  .person { position: absolute; top: 96px; left: 40px; }
  .person__name {
    font-weight: 500;
    font-size: 24px;
    letter-spacing: 1px;
    color: var(--navy);
  }
  .person__title {
    margin-top: 4px;
    font-size: 15px;
    color: var(--grey);
  }
  .contact {
    position: absolute;
    left: 40px; bottom: 30px;
    color: var(--white);
    font-size: 15px;
    line-height: 1.45;
  }
  .contact__address { margin-bottom: 10px; }
  .contact__row { display: flex; align-items: center; gap: 10px; }
  .contact__row svg { width: 14px; height: 14px; flex: none; }
  .contact__web strong { font-weight: 700; }
  .back-circle {
    position: absolute;
    right: 26px; top: 118px;
    width: 170px; height: 170px;
    border-radius: 50%;
    border: 14px solid var(--sky);
    background: var(--white);
  }
</style>
</head>
<body>

<section class="card card--front">
  <div class="front-mark">
    <div class="front-mark__circle"></div>
    <div class="front-mark__name">SKYVORNQ</div>
  </div>
  <div class="front-url">www.<strong>skyvornq</strong>.com</div>
</section>

<section class="card card--back">
  <svg class="back-band" viewBox="0 0 620 354" preserveAspectRatio="none" aria-hidden="true">
    <defs>
      <linearGradient id="bandFill" x1="0" y1="0" x2="1" y2="0">
        <stop offset="0" stop-color="#1c3163"/>
        <stop offset="0.45" stop-color="#2b4478"/>
        <stop offset="1" stop-color="#14264f"/>
      </linearGradient>
    </defs>
    <polygon points="0,210 620,110 620,354 0,354" fill="url(#bandFill)"/>
  </svg>

  <div class="back-wordmark">SKYVORNQ</div>

  <div class="person">
    <div class="person__name">DANIEL HARTWELL</div>
    <div class="person__title">Director</div>
  </div>

  <div class="contact">
    <div class="contact__address">4827 Trellis Hollow Road,<br>Corvale Bay, Westmarch, 34951</div>
    <div class="contact__row">
      <svg viewBox="0 0 24 24"><path fill="#fff" d="M6.6 10.8a15 15 0 0 0 6.6 6.6l2.2-2.2a1 1 0 0 1 1-.25 11.4 11.4 0 0 0 3.6.57 1 1 0 0 1 1 1V20a1 1 0 0 1-1 1A17 17 0 0 1 3 4a1 1 0 0 1 1-1h3.5a1 1 0 0 1 1 1c0 1.25.2 2.45.57 3.6a1 1 0 0 1-.25 1z"/></svg>
      <span>555-218-7340</span>
    </div>
    <div class="contact__row">
      <svg viewBox="0 0 24 24"><rect x="3" y="5" width="18" height="14" rx="2" fill="none" stroke="#fff" stroke-width="2"/><path d="M3 7l9 6 9-6" fill="none" stroke="#fff" stroke-width="2"/></svg>
      <span>info@skyvornq.com</span>
    </div>
    <div class="contact__row contact__web">
      <svg viewBox="0 0 24 24"><circle cx="12" cy="12" r="9" fill="none" stroke="#fff" stroke-width="2"/><path d="M3 12h18M12 3c3 3.5 3 14.5 0 18M12 3c-3 3.5-3 14.5 0 18" fill="none" stroke="#fff" stroke-width="1.6"/></svg>
      <span>www.<strong>skyvornq</strong>.com</span>
    </div>
  </div>

  <div class="back-circle"></div>
</section>

</body>
</html>
```